Harbinger Water Shield, Inc

I need the following
Logo
Truck wrap
We are a new flood protection company for residential homes and commercial businesses in Florida that is designed to keep flood waters from entering entry points
It is a rubber gasketed aluminum barrier system with permanent brackets installed to masonry structures.
We want to consider including a photo of an installation on our vehicles.
We would like the font to be legible from a distance yet have the tailgates be read easily at a traffic light. We are open to color selection but we want to differentiate from others.
No super hero stuff, no gimmicky nonsense - just super clean and not busy. Need to be memorable. Less is more.
Can show flooding but NO WAVES

See attached photos of similar installations

```html
<!DOCTYPE html>
<html lang="en">
<head>
<meta charset="utf-8">
<title>Harbinger Water Shield, Inc — Truck Wrap Panels</title>
<link rel="stylesheet" href="https://fonts.googleapis.com/css2?family=Montserrat:ital,wght@0,600;0,700;1,700;1,800&display=swap">
<style>
  :root {
    --stage: #eceef1;
    --navy: #123659;
    --navy-deep: #0c2a48;
    --navy-mid: #1d5683;
    --accent: #2a93cf;
    --white: #ffffff;
    --ink: #1b1e24;
    --frame: #c9ced4;
    --photo-a: #b9c6cf;
    --photo-b: #4f86a3;
    --photo-c: #8a9aa3;
  }
  * { margin: 0; padding: 0; box-sizing: border-box; }
  html, body {
    width: 1200px;
    height: 3625px;
    overflow: hidden;
    background: var(--stage);
  }
  .sheet {
    display: grid;
    grid-template-rows: repeat(4, 906.25px);
    width: 1200px;
    height: 3625px;
  }
  .view {
    display: flex;
    align-items: center;
    justify-content: center;
  }
  .panel { display: block; filter: drop-shadow(0 6px 14px rgba(20, 40, 60, .12)); }
  .brand-name { font-family: "Montserrat", sans-serif; font-weight: 600; fill: var(--ink); }
  .brand-name--dark { fill: var(--navy-deep); }
  .phone-number { font-family: "Montserrat", sans-serif; font-weight: 800; font-style: italic; fill: var(--white); }
  .logo-mark { fill: var(--navy); }
  .photo-ring { stroke: var(--white); stroke-width: 6; }
  .panel-frame { fill: none; stroke: var(--frame); stroke-width: 4; }
</style>
</head>
<body>
<main class="sheet">

  <!-- Front header of the cargo box -->
  <section class="view view--front">
    <svg class="panel panel--front" width="600" height="215" viewBox="0 0 600 215" aria-label="Front header panel">
      <rect width="600" height="215" fill="var(--white)"/>
      <rect class="logo-mark" x="40" y="50" width="110" height="110" rx="6"/>
      <text class="brand-name" x="180" y="117" font-size="27">Harbinger Water Shield, Inc</text>
      <rect class="panel-frame" x="2" y="2" width="596" height="211"/>
    </svg>
  </section>

  <!-- Curb side of the cargo box -->
  <section class="view view--curb-side">
    <svg class="panel panel--side" width="1060" height="485" viewBox="0 0 1060 485" aria-label="Curb side panel">
      <defs>
        <linearGradient id="navyFill" x1="0" y1="0" x2="1" y2="1">
          <stop offset="0" stop-color="var(--navy-deep)"/>
          <stop offset=".6" stop-color="var(--navy)"/>
          <stop offset="1" stop-color="var(--navy-mid)"/>
        </linearGradient>
        <path id="sideSweep" d="M300 0 H1060 V230 C900 170 700 170 560 230 C450 280 340 270 290 200 C260 150 270 60 300 0 Z"/>
      </defs>
      <rect width="1060" height="485" fill="url(#navyFill)"/>
      <use href="#sideSweep" fill="var(--accent)" transform="translate(-22 20)"/>
      <use href="#sideSweep" fill="var(--white)"/>
      <circle class="photo-ring" cx="107" cy="115" r="90" fill="var(--photo-a)" role="img" aria-label="Photo of a barrier installed at a home doorway"/>
      <circle class="photo-ring" cx="150" cy="282" r="102" fill="var(--photo-b)" role="img" aria-label="Photo of a protected waterfront home with pool"/>
      <circle class="photo-ring" cx="272" cy="378" r="80" fill="var(--photo-c)" role="img" aria-label="Photo of an aluminum barrier at a garage entry"/>
      <rect class="logo-mark" x="318" y="102" width="120" height="120" rx="6"/>
      <text class="brand-name" x="478" y="176" font-size="36">Harbinger Water Shield, Inc</text>
      <g class="phone-icon" transform="translate(488 348) scale(2.1)" fill="none" stroke="var(--white)" stroke-width="2.4" stroke-linejoin="round">
        <path d="M6 2h4l2 5-3 2a11 11 0 0 0 6 6l2-3 5 2v4a2 2 0 0 1-2 2A18 18 0 0 1 4 4a2 2 0 0 1 2-2z"/>
      </g>
      <text class="phone-number" x="552" y="395" font-size="62">0198-765-432</text>
      <rect class="panel-frame" x="2" y="2" width="1056" height="481"/>
    </svg>
  </section>

  <!-- Rear roll-up door -->
  <section class="view view--rear">
    <svg class="panel panel--rear" width="520" height="460" viewBox="0 0 520 460" aria-label="Rear door panel">
      <defs>
        <linearGradient id="rearFill" x1="0" y1="0" x2="0" y2="1">
          <stop offset="0" stop-color="var(--navy-mid)"/>
          <stop offset="1" stop-color="var(--navy-deep)"/>
        </linearGradient>
        <path id="rearSweep" d="M0 0 H520 V30 C500 230 380 290 260 290 C140 290 20 230 0 30 Z"/>
      </defs>
      <rect width="520" height="460" fill="url(#rearFill)"/>
      <use href="#rearSweep" fill="var(--accent)" transform="translate(0 14)"/>
      <use href="#rearSweep" fill="var(--white)"/>
      <rect class="logo-mark" x="180" y="60" width="160" height="160" rx="8"/>
      <rect x="42" y="308" width="436" height="44" rx="8" fill="var(--white)"/>
      <text class="brand-name brand-name--dark" x="260" y="338" font-size="23" text-anchor="middle">Harbinger Water Shield, Inc</text>
      <g class="phone-icon" transform="translate(108 376) scale(1.15)" fill="none" stroke="var(--white)" stroke-width="2.4" stroke-linejoin="round">
        <path d="M6 2h4l2 5-3 2a11 11 0 0 0 6 6l2-3 5 2v4a2 2 0 0 1-2 2A18 18 0 0 1 4 4a2 2 0 0 1 2-2z"/>
      </g>
      <text class="phone-number" x="145" y="402" font-size="34">0198-765-432</text>
      <rect class="panel-frame" x="2" y="2" width="516" height="456"/>
    </svg>
  </section>

  <!-- Street side of the cargo box -->
  <section class="view view--street-side">
    <svg class="panel panel--side" width="1060" height="485" viewBox="0 0 1060 485" aria-label="Street side panel">
      <rect width="1060" height="485" fill="url(#navyFill)"/>
      <g transform="translate(1060 0) scale(-1 1)">
        <use href="#sideSweep" fill="var(--accent)" transform="translate(-22 20)"/>
        <use href="#sideSweep" fill="var(--white)"/>
      </g>
      <circle class="photo-ring" cx="953" cy="115" r="90" fill="var(--photo-a)" role="img" aria-label="Photo of a barrier installed at a home doorway"/>
      <circle class="photo-ring" cx="910" cy="282" r="102" fill="var(--photo-b)" role="img" aria-label="Photo of a protected waterfront home with pool"/>
      <circle class="photo-ring" cx="788" cy="378" r="80" fill="var(--photo-c)" role="img" aria-label="Photo of an aluminum barrier at a garage entry"/>
      <rect class="logo-mark" x="46" y="70" width="122" height="122" rx="6"/>
      <text class="brand-name" x="212" y="146" font-size="36">Harbinger Water Shield, Inc</text>
      <g class="phone-icon" transform="translate(48 348) scale(2.1)" fill="none" stroke="var(--white)" stroke-width="2.4" stroke-linejoin="round">
        <path d="M6 2h4l2 5-3 2a11 11 0 0 0 6 6l2-3 5 2v4a2 2 0 0 1-2 2A18 18 0 0 1 4 4a2 2 0 0 1 2-2z"/>
      </g>
      <text class="phone-number" x="112" y="395" font-size="62">0198-765-432</text>
      <rect class="panel-frame" x="2" y="2" width="1056" height="481"/>
    </svg>
  </section>

</main>
</body>
</html>
```